Email Marketing Campaign Brief

We want to do an email marketing campaign around our consulting services. The attached documents provide back ground on our work but additional copy can be found below:

KV7lr is committed to helping you, the educator, make informed buying decisions based on local control and independent reviews through a simple, impartial and an effective approach.
In education, there exists a vast array of educational solutions – such as reading, science, language arts, and math curricula; school-wide reform programs; interventions; after-school programs; and new educational technologies. In the marketplace, providers could, and most do, claim to be able to improve educational outcomes and, in many cases, they all pretend to be supported by evidence. But a cursory review reveals that most evidence consists of poorly designed or advocacy-driven studies with some providers having such inadequate research as could only be described as case studies.

So the problem for State and local education officials is that they must sort through a myriad of such claims to decide which solutions merit consideration for their schools and classrooms. One US official stated the problem saying “many of these practitioners have seen interventions (solutions), introduced with great fanfare as being able to produce dramatic gains, come and go over the years, yielding little in the way of positive and lasting change – a perception confirmed by the flat achievement results over the past 30 years in the Federal Survey of Scholastic Attainment long-term trend”

KV7lr is a process by which we make you, the educator, the locus of control

OUR Approach:
With four simple, yet highly effective steps, KV7lr guides educators through an informed buying process that’s based on local control and review.

Step 1 — Research, Review, and Evaluation Criteria

Step 2 — Cost / Benefit Analysis

Step 3 — Education Survey & Culture Scan

Step 4 — Negotiation & Representation

Target Market(s)

Education

Industry/Entity Type

Marketing

Font styles to use
Sans Serif

Colors
f9b46a
f37122

Requirements
Must have
• HTML format that can be used in an Email Campaign
Nice to have
• Additional Copy in Word

```html
<!DOCTYPE html>
<html lang="en">
<head>
<meta charset="utf-8">
<title>KV7lr – Informed Buying for Educators</title>
<link rel="stylesheet" href="https://fonts.googleapis.com/css2?family=Baloo+2:wght@600;700;800&family=Quicksand:wght@300;400;500&family=Open+Sans:wght@400;600;700&display=swap">
<style>
  :root{
    --orange:#f37122;
    --peach:#f9b46a;
    --red:#d6353a;
    --cyan:#1cb4e4;
    --green:#1f7d5e;
    --card-orange:#e9521f;
    --card-blue:#179fda;
    --card-yellow:#f9a11a;
    --number:#e2384a;
    --ink:#333;
    --muted:#555;
    --white:#fff;
  }
  *{margin:0;padding:0;box-sizing:border-box}
  html,body{width:702px;height:1200px;overflow:hidden;background:var(--white)}
  body{position:relative;font-family:"Open Sans",Arial,sans-serif;color:var(--ink)}
  .abs{position:absolute}

  /* header */
  .tab{position:absolute;top:0;height:52px;display:flex;align-items:center;justify-content:center;
       font-family:"Baloo 2",Arial,sans-serif;font-weight:700;font-size:19px;color:var(--white)}
  .tab-research{left:216px;width:188px;background:var(--card-yellow);clip-path:polygon(0 0,100% 0,90% 100%,0 100%)}
  .tab-policy{left:382px;width:184px;background:var(--red);clip-path:polygon(10% 0,100% 0,90% 100%,0 100%)}
  .tab-practice{left:542px;width:160px;background:var(--cyan);clip-path:polygon(11% 0,100% 0,100% 100%,0 100%);padding-left:14px}
  .brand-block{position:absolute;left:0;top:26px;width:242px;height:78px;background:var(--orange);
       clip-path:polygon(0 0,90% 0,100% 50%,90% 100%,0 100%);display:flex;align-items:center;padding-left:44px;gap:9px}
  .brand-dot{width:18px;height:18px;border-radius:50%;background:var(--white)}
  .brand-name{font-family:"Quicksand",Arial,sans-serif;font-weight:400;font-size:32px;color:var(--white);letter-spacing:.5px}

  /* hero */
  .hero{position:absolute;left:24px;top:76px;width:654px;height:310px}
  .hero-title{position:absolute;left:0;width:702px;top:310px;text-align:center;font-family:"Baloo 2",Arial,sans-serif;
       font-weight:700;font-size:27px;color:var(--white);text-shadow:0 2px 4px rgba(0,0,0,.55)}
  .hero-sub{position:absolute;left:0;width:702px;top:346px;text-align:center;font-family:"Baloo 2",Arial,sans-serif;
       font-weight:700;font-size:18px;color:var(--white);text-shadow:0 2px 4px rgba(0,0,0,.55)}

  /* intro copy */
  .intro{position:absolute;top:399px;width:286px;font-size:6.6px;line-height:1.36;text-align:justify;color:var(--ink)}
  .intro p{margin-bottom:0}
  .intro .gap{margin-top:5px}
  .intro-left{left:56px}
  .intro-right{left:360px}
  .brand-inline{color:var(--orange);font-weight:700}

  /* approach */
  .approach-title{position:absolute;top:506px;left:0;width:702px;text-align:center;font-family:"Baloo 2",Arial,sans-serif;
       font-weight:800;font-size:17px;color:var(--ink)}
  .approach-sub{position:absolute;top:525px;left:0;width:702px;text-align:center;font-family:"Quicksand",Arial,sans-serif;
       font-size:10.5px;line-height:1.25;color:var(--muted)}

  .cards-art{position:absolute;left:0;top:0}
  .step-num{position:absolute;width:52px;height:52px;border-radius:50%;background:var(--white);border:3px solid var(--card-orange);
       display:flex;align-items:center;justify-content:center;font-family:"Baloo 2",Arial,sans-serif;font-weight:800;
       font-size:33px;color:var(--number);line-height:1;padding-top:4px}
  .card-title{position:absolute;font-family:"Quicksand",Arial,sans-serif;font-weight:400;font-size:17px;line-height:1.2;
       color:var(--white);text-transform:uppercase;text-align:center}
  .card-list{position:absolute;list-style:none;font-family:"Quicksand",Arial,sans-serif;font-weight:500;font-size:9px;
       line-height:1.25;color:var(--white)}
  .card-list li{position:relative;padding-left:10px}
  .card-list li::before{content:"";position:absolute;left:0;top:2px;width:6px;height:6px;border-radius:50%;background:var(--white)}
  .card-list.spaced li{margin-bottom:12px}
  .card-list.centered{text-align:center}
  .card-list.centered li{padding-left:0}
  .card-list.centered li::before{position:static;display:inline-block;margin-right:4px;vertical-align:0}
  .read-more{position:absolute;height:21px;background:var(--white);color:var(--card-orange);font-family:"Quicksand",Arial,sans-serif;
       font-weight:500;font-size:10.5px;display:flex;align-items:center;justify-content:center;width:66px}

  /* implementation */
  .rule{position:absolute;left:162px;width:366px;height:1px;background:#666}
  .impl-title{position:absolute;top:1010px;left:0;width:702px;text-align:center;font-family:"Baloo 2",Arial,sans-serif;
       font-weight:800;font-size:22px;color:var(--orange);letter-spacing:.3px}
  .impl-sub{position:absolute;top:1036px;left:0;width:702px;text-align:center;font-family:"Quicksand",Arial,sans-serif;
       font-weight:500;font-size:13px;color:var(--ink)}
  .cta-line{position:absolute;left:0;width:702px;text-align:center;font-size:11.5px;color:var(--ink)}
  .cta-line strong{font-weight:700}

  /* footer */
  .footer-bar{position:absolute;left:50px;top:1112px;width:608px;height:48px;background:var(--orange);
       border-top:3px solid var(--peach);display:flex;align-items:center;padding-left:12px}
  .footer-q{font-family:"Quicksand",Arial,sans-serif;font-size:10px;color:var(--white)}
  .footer-phone{font-family:"Baloo 2",Arial,sans-serif;font-weight:700;font-size:15px;color:var(--white);margin-left:9px}
  .social{position:absolute;top:10px;width:25px;height:25px;border-radius:4px;background:var(--white)}
  .site{position:absolute;top:1164px;left:516px;font-size:10.5px;font-weight:600;color:var(--ink)}
</style>
</head>
<body>

<header>
  <div class="tab tab-research">Research</div>
  <div class="tab tab-policy">Policy</div>
  <div class="tab tab-practice">Practice</div>
  <div class="brand-block"><span class="brand-dot"></span><span class="brand-name">KV7lr</span></div>
</header>

<svg class="abs" style="left:0;top:0" width="702" height="400" aria-hidden="false">
  <defs>
    <linearGradient id="heroTone" x1="0" y1="0" x2="1" y2="1">
      <stop offset="0" stop-color="#c9b49a"/>
      <stop offset=".45" stop-color="#d7a98f"/>
      <stop offset=".75" stop-color="#8fa8c4"/>
      <stop offset="1" stop-color="#a763b6"/>
    </linearGradient>
  </defs>
  <path role="img" aria-label="Photo of young children sitting on a classroom floor listening to a teacher"
        d="M24,76 H678 V360 Q520,384 351,381 Q180,378 24,352 Z" fill="url(#heroTone)"/>
</svg>
<div class="hero-title">We help you to build geniuses</div>
<div class="hero-sub">Research, Teaching, Learning</div>

<section class="intro intro-left">
  <p><span class="brand-inline">KV7lr</span> is committed to helping you, the educator; make informed buying decisions based on local control and independent reviews through a simple, impartial and an effective approach.</p>
  <p>In education, there exists a vast array of educational solutions – such as reading, science, language arts, and math curricula; school-wide reform programs; interventions; after-school programs; and new educational technologies. In the marketplace, providers could, and most do, claim to be able to improve educational outcomes and, in many cases, they all pretend to be supported by evidence. But a cursory review reveals that most evidence consists of poorly designed or advocacy-driven studies with some providers having such inadequate research as could only be described as case studies.</p>
</section>
<section class="intro intro-right">
  <p>So the problem for State and local education officials is that they must sort through a myriad of such claims to decide which solutions merit consideration for their schools and classrooms.</p>
  <p>One US official stated the problem saying “many of these practitioners have seen interventions (solutions), introduced with great fanfare as being able to produce dramatic gains, come and go over the years, yielding little in the way of positive and lasting change – a perception confirmed by the flat achievement results over the past 30 years in the Federal Survey of Scholastic Attainment long-term trend”.</p>
  <p class="gap"><span class="brand-inline">KV7lr</span> is a process by which we make you, the educator, the focus of control.</p>
</section>

<div class="approach-title">OUR Approach:</div>
<div class="approach-sub">With four simple, yet highly effective steps, KV7lr guides educators through<br>an informed buying process that’s based on local control and review.</div>

<svg class="cards-art" width="702" height="1010" aria-hidden="true">
  <path d="M24,582 Q58,560 100,574 Q140,588 172,568 Q204,550 232,566 L232,852 L24,852 Z" fill="var(--green)"/>
  <path d="M470,566 Q500,550 532,568 Q566,588 606,574 Q646,560 686,582 L686,852 L470,852 Z" fill="var(--card-blue)"/>
  <path d="M244,598 L262,594 L280,598 L300,593 L322,597 L346,594 L372,598 L398,593 L420,597 L440,594 L458,597 L458,824 L244,824 Z" fill="var(--card-orange)"/>
  <path d="M196,822 L502,822 Q512,822 512,832 L510,956 Q510,964 500,964 L200,964 Q190,964 190,956 L188,832 Q188,822 196,822 Z" fill="var(--card-yellow)"/>
  <!-- magnifier -->
  <circle cx="44" cy="804" r="8" fill="none" stroke="#fff" stroke-width="2"/>
  <line x1="50" y1="810" x2="58" y2="820" stroke="#fff" stroke-width="2.5" stroke-linecap="round"/>
  <!-- bulb -->
  <circle cx="298" cy="774" r="7" fill="none" stroke="#fff" stroke-width="1.8"/>
  <rect x="295" y="781" width="6" height="5" fill="#fff"/>
  <g stroke="#fff" stroke-width="1.5" stroke-linecap="round">
    <line x1="298" y1="761" x2="298" y2="764"/><line x1="285" y1="774" x2="288" y2="774"/>
    <line x1="308" y1="774" x2="311" y2="774"/><line x1="289" y1="765" x2="291" y2="767"/>
    <line x1="307" y1="765" x2="305" y2="767"/>
  </g>
  <!-- gear -->
  <circle cx="552" cy="811" r="8" fill="none" stroke="#fff" stroke-width="3" stroke-dasharray="3 2"/>
  <circle cx="552" cy="811" r="5" fill="none" stroke="#fff" stroke-width="1.8"/>
  <!-- laptop -->
  <rect x="278" y="932" width="26" height="16" rx="1" fill="none" stroke="#fff" stroke-width="1.8"/>
  <path d="M272,950 H310 L307,954 H275 Z" fill="#fff"/>
  <!-- divider & pointer -->
  <line x1="162" y1="974.5" x2="528" y2="974.5" stroke="#555" stroke-width="1"/>
  <path d="M272,976 L432,976 L352,1004 Z" fill="var(--peach)"/>
</svg>

<section aria-label="Step 1">
  <div class="step-num" style="left:26px;top:546px">1</div>
  <h3 class="card-title" style="left:24px;top:612px;width:208px">Research, Review, and<br>Evaluation Criteria</h3>
  <ul class="card-list spaced" style="left:32px;top:662px;width:196px">
    <li>District needs analysis</li>
    <li>Program reviews and alignment to need</li>
    <li>Independent evaluation / data informed decisions</li>
  </ul>
  <div class="read-more" style="left:68px;top:801px">READ MORE</div>
</section>

<section aria-label="Step 2">
  <div class="step-num" style="left:324px;top:576px">2</div>
  <h3 class="card-title" style="left:244px;top:633px;width:214px">Cost / Benefit Analysis</h3>
  <ul class="card-list spaced" style="left:258px;top:662px;width:196px">
    <li>Cost alignment based on research, review and evaluation of programs</li>
    <li>Program cost by product offering and alignment to identified needs</li>
    <li>Summary of cost, data and return on investment</li>
  </ul>
  <div class="read-more" style="left:318px;top:766px">READ MORE</div>
</section>

<section aria-label="Step 3">
  <div class="step-num" style="left:614px;top:546px">3</div>
  <h3 class="card-title" style="left:470px;top:612px;width:216px">Education Survey<br>and Culture Scan</h3>
  <ul class="card-list spaced" style="left:484px;top:662px;width:202px">
    <li>District observation and perception survey</li>
    <li>Culture scan to identify education best practices</li>
    <li>Match to strategic plan goals and objectives</li>
  </ul>
  <div class="read-more" style="left:574px;top:801px">READ MORE</div>
</section>

<section aria-label="Step 4">
  <div class="step-num" style="left:324px;top:796px">4</div>
  <h3 class="card-title" style="left:188px;top:846px;width:324px">Negotiation<br>and Representation</h3>
  <ul class="card-list centered" style="left:188px;top:895px;width:324px">
    <li>Conduct Provider review and presentation</li>
    <li>Representation for content and program negotiations</li>
    <li>Support district in independent decision-making process</li>
  </ul>
  <div class="read-more" style="left:316px;top:934px">READ MORE</div>
</section>

<div class="impl-title">PROGRAM IMPLEMENTATION</div>
<div class="impl-sub">Independent Review Connected to School District Need and Stakeholder</div>
<div class="rule" style="top:1060px"></div>
<div class="cta-line" style="top:1070px">Let <span class="brand-inline">KV7lr</span> help you make informed buying decisions.</div>
<div class="cta-line" style="top:1085px"><strong>Contact us today for a no-cost consultation</strong></div>

<footer class="footer-bar">
  <span class="footer-q">Have a question? It is great to listen to you:</span>
  <span class="footer-phone">555.210.4477</span>
  <span class="social" style="left:450px"></span>
  <span class="social" style="left:481px"></span>
  <span class="social" style="left:512px"></span>
  <span class="social" style="left:543px"></span>
</footer>
<div class="site">www.KV7lr.com</div>

</body>
</html>
```